Simple templates for management consulting firm

Vireo Advisors is a management consulting firm based in the DC area. We have all the basic templates but would like to tweak them so they look consistent.

Check us out at www.vireoadvisors.example

For this project we would like to get
a tweaked powerpoint template (header should be up)
a letter template for letters
a fax template

Current templates and our logo are attached.
Updates

We just increased the budget of this project.

We got questions about the project. Here are our thoughts on this one:

Please include the logo into the fax template. If you find improvements in the layout then feel free to make those. Let's not overthink this too much. Keep it simple :)

We like The powerpoint concept as is. The slide titles are for some reasons on the bottom. It seems to irritate some folks. If you can switch the slide titles to the top, keep the look and feel of the slides and work in the logo then that would be fantastic.

The letter head should include the following

Vireo Advisors, LLC Box 5827, Great Falls, VA 20471 Phone 703 555-0148, Fax 703 555 0193, www.vireoadvisors.example and the logo.

Again, let's keep it simple.

Thank you for considering this project.

We just realize that we are not necessarily inisting to use the red in the slides.
Any approach that would work with the logo will be considered.

Thanks for your creativity.

Target Market(s)

tech companies, Meridian 400, venture capitalists

Industry/Entity Type

Management Consulting

Requirements
Must have
• Keep it simple please

```html
<!DOCTYPE html>
<html lang="en">
<head>
<meta charset="utf-8">
<title>Getting Projects DONE – Vireo Advisors</title>
<link rel="stylesheet" href="https://fonts.googleapis.com/css2?family=Fira+Sans:wght@700;800&family=Fira+Sans+Condensed:ital,wght@0,400;1,700&display=swap">
<style>
  :root {
    --bg-light: #ffffff;
    --bg-edge: #c9c9c9;
    --title-grey: #8d8d8d;
    --title-shadow: #4a4a4a;
    --gold: #f0c23c;
    --gold-light: #f8e3a0;
    --gold-dark: #c99a1a;
    --arrow-shadow: #2e2e2e;
    --label: #5a4a2a;
    --brand: #a8894a;
    --brand-mark: #8f8f8f;
    --rule: #9a9a9a;
    --legal: #333333;
  }
  * { margin: 0; padding: 0; box-sizing: border-box; }
  html, body { width: 1200px; height: 816px; overflow: hidden; }
  body {
    position: relative;
    background: radial-gradient(ellipse 75% 80% at 48% 48%, var(--bg-light) 0%, #ececec 45%, var(--bg-edge) 100%);
    font-family: "Fira Sans", sans-serif;
  }
  .slide-title {
    position: absolute;
    left: 92px;
    top: 16px;
    font-family: "Fira Sans", sans-serif;
    font-weight: 800;
    font-size: 88px;
    letter-spacing: 1px;
    color: var(--title-grey);
    text-shadow: 2px 3px 4px var(--title-shadow), -1px -1px 0 #d6d6d6;
    white-space: nowrap;
  }
  .title-bar {
    position: absolute;
    left: 91px;
    top: 130px;
    width: 810px;
    height: 14px;
    background: linear-gradient(var(--gold-light), var(--gold) 50%, var(--gold-dark));
    box-shadow: 3px 5px 4px rgba(0,0,0,0.55);
  }
  .brand {
    position: absolute;
    left: 922px;
    top: 108px;
    display: flex;
    align-items: center;
    gap: 12px;
  }
  .brand-mark {
    width: 52px;
    height: 52px;
    border-radius: 50%;
    background: var(--brand-mark);
  }
  .brand-name {
    font-family: "Fira Sans", sans-serif;
    font-weight: 700;
    font-size: 26px;
    color: var(--brand);
  }
  .process {
    position: absolute;
    left: 0;
    top: 0;
  }
  .step-label {
    font-family: "Fira Sans Condensed", sans-serif;
    font-style: italic;
    font-weight: 700;
    font-size: 42px;
    fill: var(--label);
  }
  .footer-rule {
    position: absolute;
    left: 49px;
    top: 749px;
    width: 1067px;
    height: 1px;
    background: var(--rule);
  }
  .legal {
    position: absolute;
    left: 20px;
    top: 754px;
    width: 1160px;
    text-align: center;
    font-family: "Fira Sans Condensed", sans-serif;
    font-size: 17px;
    line-height: 17px;
    color: var(--legal);
  }
</style>
</head>
<body>
  <h1 class="slide-title">Getting Projects DONE</h1>
  <div class="title-bar"></div>

  <div class="brand">
    <span class="brand-mark"></span>
    <span class="brand-name">Vireo Advisors</span>
  </div>

  <svg class="process" width="1200" height="816" viewBox="0 0 1200 816" aria-label="Project process: PreWork, Plan, Execute, Assess">
    <defs>
      <linearGradient id="goldFill" x1="0" y1="0" x2="0" y2="1">
        <stop offset="0" stop-color="#fbe9a8"/>
        <stop offset="0.5" stop-color="#f2c84a"/>
        <stop offset="1" stop-color="#d9a825"/>
      </linearGradient>
      <filter id="softShadow" x="-20%" y="-20%" width="140%" height="140%">
        <feGaussianBlur stdDeviation="4"/>
      </filter>
      <polygon id="arrowShape" points="0,0 139,-22 139,-74 279,0 139,74 139,22"/>
    </defs>

    <g class="step" transform="translate(49,384)">
      <use href="#arrowShape" fill="var(--arrow-shadow)" transform="translate(24,16)" filter="url(#softShadow)"/>
      <use href="#arrowShape" fill="url(#goldFill)"/>
      <text class="step-label" x="150" y="14" text-anchor="middle">PreWork</text>
    </g>
    <g class="step" transform="translate(328,391)">
      <use href="#arrowShape" fill="var(--arrow-shadow)" transform="translate(24,16)" filter="url(#softShadow)"/>
      <use href="#arrowShape" fill="url(#goldFill)"/>
      <text class="step-label" x="165" y="14" text-anchor="middle">Plan</text>
    </g>
    <g class="step" transform="translate(605,398)">
      <use href="#arrowShape" fill="var(--arrow-shadow)" transform="translate(24,16)" filter="url(#softShadow)"/>
      <use href="#arrowShape" fill="url(#goldFill)"/>
      <text class="step-label" x="153" y="14" text-anchor="middle">Execute</text>
    </g>
    <g class="step" transform="translate(881,405)">
      <use href="#arrowShape" fill="var(--arrow-shadow)" transform="translate(24,16)" filter="url(#softShadow)"/>
      <use href="#arrowShape" fill="url(#goldFill)"/>
      <text class="step-label" x="158" y="14" text-anchor="middle">Assess</text>
    </g>
  </svg>

  <div class="footer-rule"></div>
  <p class="legal">Copyright © 2012 by Vireo Advisors, LLC. All rights reserved. This document contains confidential and proprietary information and may not be<br>reproduced, in whole or in part, without express written permission from Vireo Advisors, LLC.</p>
</body>
</html>
```